New business card, letter head, email signature and Portfolio for our Security company.

We are an Crest security company that provides a top quality manpower services to protect high rise buildings, retail and all type of properties and would like a new business card/logo look.

- We would like the spot UV design.
- Matt black (double sided).
- We would like to incorporate a royal blue colour (feel free to experiment with it).
- Feel free to try different lengths with the card to make it stand out more than a normal business card.
- We would like the logo to be an eagle eye in the background (shines when card is tilted slightly in the background, either on the front, back or both sides of the card). Image attached as an example of eye shape (colour to be either black or royal blue).
- HARBOUR CREST SECURITY SERVICES PTY. LTD. and HCSS to be placed on one side of the card and on the other side of the card to have;

- Name in slightly bigger font than the position (directly on the bottom on the name).
- Mobile number
- Email address
- Website email address
- PO BOX address

Can we please have the files in a format that we can edit.

Reason: I need to consult my business partner with the designs so far and will make a decision from there.

Target Market(s)

Security Industry

Industry/Entity Type

Business

Contact Information for Business Card

- Mobile number
- Email address
- Website email address
- PO BOX address

Logo Text

HCSS and underneath the HCSS please add HARBOUR CREST SECURITY SERVICES PTY. LTD.

Font styles to use
Other font styles liked:
• bold type font

Colors
0255a3
000000

Requirements
Must have
• We are an Crest security company that provides a top quality manpower services to protect high rise buildings, retail and all type of properties and would like a new business card/logo look.
• - We would like the spot UV design.
• - Matt black (double sided).
• - We would like to incorporate a royal blue colour (feel free to experiment with it).
• - Feel free to try different lengths with the card to make it stand out more than a normal business card.
• - We would like the logo to be an eagle eye in the background (shines when card is tilted slightly in the background, either on the front, back or both sides of the card). Image attached as an example of eye shape (colour to be either black or royal blue).
• - HARBOUR CREST SECURITY SERVICES PTY. LTD. and HCSS to be placed on one side of the card and on the other side of the card to have;
• - Name in slightly bigger font than the position (directly on the bottom on the name).
• - Mobile number
• - Email address
• - Website email address
• - PO BOX address
• Can we please have the files in a format that we can edit.
Nice to have
• Feel free to try different lengths with the card to make it stand out more than a normal business card.
• Please find "URBAN JUNGLE" font attached and incorporate HCSS into the same style with building's inside the HCSS bold front also add HARBOUR into the bottom part of the S and follow on E - Crest on the bottom S - SECURITY on the bottom S - SERVICES on the bottom of each letter.
• other than that, I'll be happy with a bold modern font for the HCSS and HARBOUR CREST SECURITY SERVICES in a bold and thinner font underneath.

```html
<!DOCTYPE html>
<html lang="en">
<head>
<meta charset="utf-8">
<title>HCSS Business Card</title>
<link href="https://fonts.googleapis.com/css2?family=Open+Sans:wght@400;600;700&display=swap" rel="stylesheet">
<style>
  :root {
    --backdrop: #2b2c2e;
    --card-black: #17191c;
    --silver: #a9b3bc;
    --white: #f4f5f6;
    --royal-blue: #0255a3;
    --rule: #d9dcdf;
  }
  * { box-sizing: border-box; margin: 0; padding: 0; }
  html, body {
    width: 1200px; height: 1189px; overflow: hidden;
    background: var(--backdrop);
    font-family: "Open Sans", Verdana, sans-serif;
  }
  .card {
    position: absolute; left: 150px;
    width: 900px; height: 510px;
    background: var(--card-black);
    border-radius: 34px;
    box-shadow: 0 18px 40px rgba(0,0,0,.55);
  }
  .card-front { top: 50px; }
  .card-back { top: 630px; }

  .brand { position: absolute; font-weight: 700; }
  .brand-mark { display: block; line-height: 1; letter-spacing: 6px; }
  .brand-line { display: block; line-height: 1.1; letter-spacing: 1px; }

  .card-front .brand { left: 0; right: 0; top: 150px; text-align: center; color: var(--silver); }
  .card-front .brand-mark { font-size: 150px; }
  .card-front .brand-line { font-size: 28px; margin-top: 14px; }

  .card-back .brand { left: 70px; top: 70px; color: var(--white); }
  .card-back .brand-mark { font-size: 118px; }
  .card-back .brand-line { font-size: 23px; margin-top: 8px; }

  .divider {
    position: absolute; left: 80px; right: 80px; top: 290px;
    height: 2px; background: var(--rule);
  }
  .person { position: absolute; right: 80px; top: 110px; text-align: right; }
  .person-name {
    font-weight: 700; font-size: 34px; color: var(--white);
    padding-bottom: 4px; border-bottom: 2px solid var(--rule);
  }
  .person-role { font-weight: 600; font-size: 22px; color: var(--royal-blue); margin-top: 2px; }

  .address {
    position: absolute; right: 80px; top: 330px; text-align: right;
    font-weight: 600; font-size: 22px; line-height: 1.4; color: var(--white);
  }
  .contacts { position: absolute; left: 80px; top: 340px; list-style: none; }
  .contact {
    display: flex; align-items: center; gap: 16px;
    font-weight: 600; font-size: 25px; color: var(--white);
    height: 42px;
  }
  .contact-icon { width: 32px; height: 32px; flex: none; }
</style>
</head>
<body>
  <section class="card card-front">
    <div class="brand">
      <span class="brand-mark">HCSS</span>
      <span class="brand-line">HARBOUR CREST SECURITY SERVICES</span>
    </div>
  </section>

  <section class="card card-back">
    <div class="brand">
      <span class="brand-mark">HCSS</span>
      <span class="brand-line">HARBOUR CREST SECURITY SERVICES</span>
    </div>

    <div class="person">
      <div class="person-name">Employee Name</div>
      <div class="person-role">Manager</div>
    </div>

    <div class="divider"></div>

    <address class="address" style="font-style:normal">
      P.O. Box 000, 4th Lane<br>Ridge Point, New Zealand
    </address>

    <ul class="contacts">
      <li class="contact">
        <svg class="contact-icon" viewBox="0 0 32 32" aria-hidden="true">
          <rect width="32" height="32" rx="5" fill="var(--royal-blue)"/>
          <path d="M11 7l4 4-2.5 2.5c1 2.5 3.5 5 6 6L21 17l4 4-3 3c-7 0-14-7-14-14z" fill="#fff"/>
        </svg>
        0123 456 789
      </li>
      <li class="contact">
        <svg class="contact-icon" viewBox="0 0 32 32" aria-hidden="true">
          <rect width="32" height="32" rx="5" fill="var(--royal-blue)"/>
          <rect x="6" y="9" width="20" height="14" fill="none" stroke="#fff" stroke-width="2"/>
          <path d="M6 9l10 8 10-8" fill="none" stroke="#fff" stroke-width="2"/>
        </svg>
        info@harbourcrestmail.net.nz
      </li>
      <li class="contact">
        <svg class="contact-icon" viewBox="0 0 32 32" aria-hidden="true">
          <rect width="32" height="32" rx="5" fill="var(--royal-blue)"/>
          <g fill="none" stroke="#fff" stroke-width="1.8">
            <circle cx="16" cy="16" r="9"/>
            <ellipse cx="16" cy="16" rx="4" ry="9"/>
            <path d="M7 16h18M9 11h14M9 21h14"/>
          </g>
        </svg>
        www.harbourcrest-guard.co.nz
      </li>
    </ul>
  </section>
</body>
</html>
```